Tarvel Kite Corporate Site Template/Blog Design

Company Info: Tarvel Kite Robotics is a San Francisco based start-up and spin-off of Halvern Drury University Robotics Institute. Our mission is to transform the consumer experience through personal robotics technology.

Our first public brand, uPickGizmos.example (UPG), used these technologies to develop engaging toy and gaming category innovations that enhance the way children play and interact with new technologies.

This assignment is about the Tarvel Kite Robotic corporate identity and not about UPG

The company is transitioning to include higher end consumer electronics and personal robotics products lines within the next few years, and we would like to establish a more formal corporate identity. Attached please find a user flow of the design needed, as well as our current logo.

High Res .EPS Link below:

https://tkrobotics.filevault.example/shared/static/a730cbe12fd9931e27ab.eps

Design Vision: Tarvel Kite Robotics is in search of a simple, clean and easily updateable corporate website with an integrated blog. The company's current public profile is primarily UPG with an emphasis our children's toy lines Wudle and Clankoras. Although you should be aware of these toy sites, please do not let them influence your design. What we are looking for is more of a blend of scientific and cool.

We would like to see a site template and design that is clean and approachable. It also needs to be able to support a CMS platform as we need the ability to allow our marketing team to update and manage content as well as add additional features such as video and ecommerce in the future as the company grows. These designs should also work well with Pagewall and Chirrup.

Attached is an image of our corporate card. The current color scheme is very basic but the design should complement them.

The final design and layout should communicate a sleek, innovative and technologically saavy consumer electronics and personal robotics company. Again, we are a consumer oriented organization but the key audiences for this site will be investors, media, retail and biz dev partners, and potential employees

Target Market(s)

Investors, Biz dev and other partners, retail, Media, employees. Consumers secondary

Industry/Entity Type

Electronics

Requirements
Must have
• The site must have all of the tabs that we have identified in the attached user flow.

The design must be able to support a backend content management system. We currently have an upgraded PageRo account, and can provide access if needed but will soon transition to our own site. we are open to your recommendations. Our objective is to be able to easily update the content without relying on a developer.

Font should be sleek. And not bubbly.
Nice to have
• Clean site design. Simple layouts. A blend between scientific and cool. Easy to navigate tabs and sub tabs. forward thinking imagery

Should not have
• Nothing complex on the Homepage- should be very simple. No cartoonish robots, bright colors. Little or no use of humans in stock photos. No competative products or copy. Toys should be under product tabs, and not featured on the homepage as in our initial design efforts we felt that the two were aesthetically polarizing. Just to confirm, the Tarvel Kite Corporate site should serve more as the parent site, and the toy lines should stay under the sub navs on the product page.

```html
<!DOCTYPE html>
<html lang="en">
<head>
<meta charset="utf-8">
<title>Tarvel Kite Robotics</title>
<link href="https://fonts.googleapis.com/css2?family=Source+Sans+3:ital,wght@0,400;0,600;0,700;1,600&display=swap" rel="stylesheet">
<style>
:root{
  --bg-top:#161616;
  --bg-body:#212121;
  --bg-footer:#121212;
  --nav-bg:#2a2a2a;
  --nav-active:#0d0d0d;
  --text:#e8e8e8;
  --text-muted:#bdbdbd;
  --orange:#e8650c;
  --orange-bright:#ff8a00;
  --panel:#3a3a3a;
  --dots:#8a8a8a;
}
*{margin:0;padding:0;box-sizing:border-box}
html,body{width:1116px;height:1200px;overflow:hidden}
body{position:relative;background:var(--bg-body);font-family:"Source Sans 3",sans-serif;color:var(--text)}
.abs{position:absolute}

.site-header{left:0;top:0;width:1116px;height:140px;background:linear-gradient(#1c1c1c,var(--bg-top))}
.top-band{left:0;top:140px;width:1116px;height:347px;background:#1b1b1b}
.brand{left:56px;top:34px;color:#f2f2f2;font-weight:700;line-height:1}
.brand-name{font-size:44px;letter-spacing:0}
.brand-sub{font-size:26px;letter-spacing:17px;margin-top:2px}

.social{display:flex;gap:12px;align-items:center}
.social-item{display:flex;align-items:center;gap:4px;font-size:12px;color:var(--text)}
.social-item .dot{width:14px;height:14px;border-radius:50%;background:#f4f4f4}
.social-top{right:46px;top:36px}
.search{left:890px;top:88px;width:180px;height:26px;background:#fafafa;border:1px solid #ccc;border-radius:2px;font-size:12px;font-style:italic;color:#999;padding:5px 8px}
.search svg{position:absolute;right:6px;top:7px}

.main-nav{left:53px;top:162px;width:1012px;height:47px;display:flex;background:linear-gradient(#333,#1e1e1e);box-shadow:0 3px 6px rgba(0,0,0,.6)}
.main-nav a{display:flex;align-items:center;justify-content:center;color:#a9a9a9;font-size:16px;text-decoration:none;border-right:1px solid #111}
.main-nav a.active{background:linear-gradient(#1a1a1a,var(--nav-active));color:#fff}

.hero{left:53px;top:230px;width:1012px;height:305px;border:2px solid var(--orange-bright);background:radial-gradient(circle at 40% 55%,#fff3c0 0,#ffb21a 12%,#ff9a0a 35%,#e45a05 80%,#c84004 100%)}
.hero-title{left:83px;top:48px;font-size:24px;font-weight:600;font-style:italic;color:#2a1607;line-height:30px}
.hero-arrows{left:22px;top:256px}

.side-list{left:66px;top:572px;list-style:none}
.side-list li{display:flex;align-items:center;gap:14px;height:32px;font-size:15px;color:var(--orange-bright)}
.side-list svg{flex:none}
.dotted{height:0;border-top:2px dotted var(--dots)}

.section-title{font-size:26px;font-weight:400;color:var(--text)}
.section-title span{color:var(--orange)}
.body-text{font-size:12.5px;line-height:21px;text-align:justify;color:var(--text)}

.news-box{left:73px;top:780px;width:229px;height:308px;background:linear-gradient(#3f3f3f,#333);border-radius:2px;box-shadow:0 2px 4px rgba(0,0,0,.5);padding:12px 15px 0}
.news-box h3{font-size:18px;font-weight:400;padding-bottom:10px;border-bottom:1px solid #666}
.news-box ul{list-style:none;margin-top:12px}
.news-box li{position:relative;padding-left:16px;font-size:12px;line-height:21px;text-align:justify;margin-bottom:12px;color:#ddd}
.news-box li::before{content:"";position:absolute;left:0;top:7px;border-left:6px solid #ddd;border-top:4px solid transparent;border-bottom:4px solid transparent}
.news-more{border-top:1px solid #666;text-align:right;font-size:12px;color:#bbb;padding-top:10px}

.card-image{width:101px;height:92px;border:1px solid #ccc}
.card-caption{font-size:13px;text-align:center;width:101px;margin-top:9px}
.card-title{font-size:14px;color:var(--orange);padding-bottom:6px;border-bottom:2px dotted #ccc;width:218px}
.card-text{font-size:12.5px;line-height:21px;text-align:justify;width:218px;margin-top:8px}

.site-footer{left:0;top:1108px;width:1116px;height:92px;background:var(--bg-footer)}
.footer-links{left:75px;top:22px;font-size:13px;color:var(--text-muted)}
.footer-links span{margin:0 7px;color:#888}
.copyright{left:75px;top:54px;font-size:13px;color:var(--text-muted)}
.social-foot{right:46px;top:38px}
</style>
</head>
<body>
<header class="site-header abs">
  <div class="brand abs"><div class="brand-name">TARVEL KITE</div><div class="brand-sub">ROBOTICS</div></div>
  <div class="social social-top abs">
    <span class="social-item"><i class="dot"></i>Pagewall</span>
    <span class="social-item"><i class="dot"></i>Chirrup</span>
    <span class="social-item"><i class="dot"></i>Searchly</span>
    <span class="social-item"><i class="dot"></i>Yodelo</span>
    <span class="social-item"><i class="dot"></i>Postmill</span>
  </div>
  <div class="search abs">Search
    <svg width="12" height="12" viewBox="0 0 12 12"><circle cx="5" cy="5" r="3.5" fill="none" stroke="#aaa" stroke-width="1.4"/><line x1="7.6" y1="7.6" x2="11" y2="11" stroke="#aaa" stroke-width="1.6"/></svg>
  </div>
</header>
<div class="top-band abs"></div>

<nav class="main-nav abs">
  <a class="active" href="#" style="width:223px">Home</a>
  <a href="#" style="width:172px">About Us</a>
  <a href="#" style="width:162px">Products</a>
  <a href="#" style="width:192px">Latest News</a>
  <a href="#" style="width:263px;border-right:0">Contact Us</a>
</nav>

<section class="hero abs" role="img" aria-label="Sunset photo of a robotic arm silhouetted beside an engineer holding a controller">
  <p class="hero-title abs">Autem vel eum iure reprehenderit<br>qui in ea voluptate velit</p>
  <svg class="hero-arrows abs" width="50" height="26" viewBox="0 0 50 26">
    <polyline points="12,3 3,13 12,23" fill="none" stroke="#2a1607" stroke-width="4"/>
    <polyline points="34,3 43,13 34,23" fill="none" stroke="#2a1607" stroke-width="4"/>
  </svg>
</section>

<ul class="side-list abs">
  <li><svg width="12" height="12"><circle cx="6" cy="6" r="6" fill="#e8650c"/><rect x="3" y="5" width="6" height="2" fill="#212121"/></svg>Etiam atdui uturna eleifend</li>
  <li><svg width="12" height="12"><circle cx="6" cy="6" r="6" fill="#e8650c"/><rect x="3" y="5" width="6" height="2" fill="#212121"/></svg>Integer tempor nisi vitae magna</li>
  <li><svg width="12" height="12"><circle cx="6" cy="6" r="6" fill="#e8650c"/><rect x="3" y="5" width="6" height="2" fill="#212121"/></svg>Nullam condimentum ultrices</li>
  <li><svg width="12" height="12"><circle cx="6" cy="6" r="6" fill="#e8650c"/><rect x="3" y="5" width="6" height="2" fill="#212121"/></svg>Vivamus a neque adiam</li>
  <li><svg width="12" height="12"><circle cx="6" cy="6" r="6" fill="#e8650c"/><rect x="3" y="5" width="6" height="2" fill="#212121"/></svg>Nullam dictum laoreet tellu</li>
</ul>

<h2 class="section-title abs" style="left:346px;top:558px"><span>Welcome</span> to Tarvel Kite</h2>
<p class="body-text abs" style="left:345px;top:601px;width:720px">Sed ut perspiciatis unde omnis iste natus error sit voluptatem accusantium doloremque laudantium, totam rem aperiam, eaque ipsa quae ab illo inventore veritatis et quasi architecto beatae vitae dicta sunt explicabo. Nemo enim ipsam voluptatem quia voluptas sit aspernatur aut odit aut fugit, sed quia consequuntur magni dolores eos qui ratione voluptatem sequi nesciunt. Neque porro quisquam est, qui dolorem ipsum quia dolor sit amet, consectetur, adipisci velit, sed quia non numquam eius modi tempora incidunt ut labore et dolore magnam aliquam quaerat voluptatem. Ut enim ad minima veniam, quis nostrum exercitationem ullam</p>

<div class="dotted abs" style="left:58px;top:751px;width:244px"></div>
<div class="dotted abs" style="left:346px;top:751px;width:719px"></div>

<aside class="news-box abs">
  <h3>Latest News</h3>
  <ul>
    <li>Ut enim ad minima veniam, quis nostrum exercitationem ullam</li>
    <li>Ut enim ad minima veniam, quis nostrum exercitationem ullam</li>
    <li>Ut enim ad minima veniam, quis nostrum exercitationem ullam</li>
    <li>Ut enim ad minima veniam, quis nostrum exercitationem ullam</li>
  </ul>
  <div class="news-more">View more</div>
</aside>

<h2 class="section-title abs" style="left:346px;top:784px"><span>About</span>&nbsp; Tarvel Kite</h2>
<p class="body-text abs" style="left:345px;top:831px;width:720px">Sed quia consequuntur magni dolores eos qui ratione voluptatem sequi nesciunt. Neque porro quisquam est, qui dolorem ipsum quia dolor sit amet, consectetur, adipisci velit, sed quia non numquam eius modi tempora incidunt ut labore et dolore magnam aliquam quaerat voluptatem quis nostrum exercitationem ullam.</p>

<article class="abs" style="left:343px;top:928px">
  <div class="card-image" role="img" aria-label="Photo of a white humanoid service robot" style="background:linear-gradient(#f2f2f4,#c9ccd4)"></div>
  <div class="card-caption">Quisque aceros</div>
</article>
<article class="abs" style="left:458px;top:926px">
  <div class="card-title">Praesent feugiat tortor vitae augue</div>
  <p class="card-text">Adipisci velit, sed quia non numquam eius modi tempora incidunt ut labore et dolore magnam aliquam quaerat voluptatum quis.</p>
</article>
<article class="abs" style="left:727px;top:928px">
  <div class="card-image" role="img" aria-label="Photo of a robotics team standing with their competition robot" style="background:linear-gradient(#8a2a22,#c8322a 60%,#e9e4e0)"></div>
  <div class="card-caption">Quisque aceros</div>
</article>
<article class="abs" style="left:842px;top:926px">
  <div class="card-title">Praesent feugiat tortor vitae augue</div>
  <p class="card-text">Adipisci velit, sed quia non numquam eius modi tempora incidunt ut labore et dolore magnam aliquam quaerat voluptatum quis.</p>
</article>

<footer class="site-footer abs">
  <div class="footer-links abs">Home<span>|</span>About us<span>|</span>Products<span>|</span>Latest News<span>|</span>Contact Us<span>|</span>Sitemap</div>
  <div class="copyright abs">Copyright © 2012 tarvelkiterobotics.example &nbsp;&nbsp;All rights reserved</div>
  <div class="social social-foot abs">
    <span class="social-item"><i class="dot"></i>Pagewall</span>
    <span class="social-item"><i class="dot"></i>Chirrup</span>
    <span class="social-item"><i class="dot"></i>Searchly</span>
    <span class="social-item"><i class="dot"></i>Yodelo</span>
    <span class="social-item"><i class="dot"></i>Postmill</span>
  </div>
</footer>
</body>
</html>
```